Business Cards for IT Consulting Company (Managed Service Provider)

I am looking to have some business cards printed and would like some designs. We are an IT Consulting company based in Vancouver BC. I would like a nice clean and modern look to the cards. I have uploaded all the versions of my logo so parts can be used as needed. Here is a snippit from our website homepage:

Quillbrook Networks Ltd. is an IT Solutions Partner located in Vancouver BC, Canada. We offer IT solutions and support to customers in the greater Vancouver Area. With expertise in Microsoft platforms, as well as Linux and Mac OSX and over 12 years experience in the IT industry, Quillbrook Networks is dedicated to offering our clients top quality service and products. We take pride in the solutions we offer our customers. The greatest compliment a client can give us is to recommend our services.

Quillbrook Networks Ltd. offers a wide range of IT services from onsite service to remote support and managed service solutions. This allows clients to choose the support path that best suits their company’s needs. Supporting many different sized companies from small to enterprise level over the past 12 years Quillbrook Networks has the experience and expertise needed to ensure things run smoothly. Allowing our clients to focus on doing business.

Revolutionizing the way IT services are delivered.

Quillbrook Networks is dedicated to providing our clients with IT solutions that work and grow with them for years to come. This philosophy helps save money in the long run instead of replacing equipment constantly. Far too often IT solutions are not well thought out and while possibly solving the problem at hand, require replacement due to growth or quality within a very short time frame. Quillbrook Networks takes pride in providing solutions that will last and be able to accommodate growth without the need for replacement.

Industry/Entity Type

Information Technology

Contact Information for Business Card

Quillbrook Networks Ltd.
(Employee Name)
Eml: (Employees Email Address)
Web: quillbrook.me
Ph: 604-555-0148

Font styles to use
Serif
Sans Serif

Requirements
Must have
• The Company logo and company colors.
Nice to have
• - Our tag line: "Revolutionizing IT Services" or "Revolutionizing the way IT services are delivered."
• - Also I really like the idea of nature and technology together blending which is sort of where my logo came from so integrating that somehow onto the business cards would be great.

```html
<!DOCTYPE html>
<html lang="en">
<head>
<meta charset="utf-8">
<title>Quillbrook Networks Ltd. — Business Cards</title>
<link rel="stylesheet" href="https://fonts.googleapis.com/css2?family=Montserrat:wght@600&family=Roboto:ital,wght@0,400;1,400&display=swap">
<style>
  :root {
    --backdrop: #b0aeaf;
    --brand-blue: #1e93d6;
    --brand-blue-deep: #1b87c9;
    --card-white: #f4f4f4;
    --ink: #3a3a3a;
    --ink-soft: #4a4a4a;
    --white: #ffffff;
  }
  * { box-sizing: border-box; margin: 0; padding: 0; }
  html, body {
    width: 1200px;
    height: 1200px;
    overflow: hidden;
    background: var(--backdrop);
  }
  .canvas {
    position: relative;
    width: 1200px;
    height: 1200px;
  }
  .card {
    position: absolute;
    width: 714px;
    height: 420px;
  }

  /* Front card */
  .card--front {
    left: 238px;
    top: 117px;
    background: var(--brand-blue);
  }
  .card__pattern {
    position: absolute;
    inset: 0;
    background: linear-gradient(180deg, #2096d8 0%, #1a8fd2 100%);
  }
  .wordmark {
    position: absolute;
    display: flex;
    align-items: center;
    gap: 16px;
    font-family: "Montserrat", Arial, sans-serif;
    font-weight: 600;
    white-space: nowrap;
  }
  .card--front .wordmark {
    left: 0;
    right: 0;
    top: 180px;
    justify-content: center;
    color: var(--white);
    font-size: 42px;
    letter-spacing: 0.5px;
  }
  .wordmark__square {
    width: 34px;
    height: 34px;
    border: 4px solid currentColor;
    flex: none;
  }

  /* Back card */
  .card--back {
    left: 230px;
    top: 643px;
    background: var(--card-white);
  }
  .card--back .wordmark {
    left: 0;
    right: 0;
    top: 88px;
    justify-content: center;
    color: var(--brand-blue);
    font-size: 40px;
    letter-spacing: 0.5px;
  }
  .person {
    position: absolute;
    right: 406px;
    top: 238px;
    text-align: right;
  }
  .person__name {
    font-family: "Montserrat", Arial, sans-serif;
    font-weight: 600;
    font-size: 24px;
    color: var(--brand-blue-deep);
    line-height: 1.2;
  }
  .person__title {
    margin-top: 4px;
    font-family: "Roboto", Arial, sans-serif;
    font-style: italic;
    font-size: 16px;
    color: var(--ink-soft);
  }
  .contact {
    position: absolute;
    left: 334px;
    top: 229px;
    list-style: none;
    font-family: "Roboto", Arial, sans-serif;
    font-size: 18px;
    color: var(--ink);
  }
  .contact__item {
    display: flex;
    align-items: center;
    gap: 16px;
    height: 27px;
  }
  .contact__icon {
    width: 20px;
    height: 16px;
    fill: var(--brand-blue-deep);
    flex: none;
  }
  .tagline {
    position: absolute;
    left: 0;
    right: 0;
    top: 364px;
    display: flex;
    align-items: center;
    justify-content: center;
    gap: 16px;
    font-family: "Roboto", Arial, sans-serif;
    font-size: 19px;
    color: var(--ink);
  }
  .tagline__rule {
    width: 108px;
    height: 3px;
    background: var(--brand-blue);
    border-radius: 2px;
  }
</style>
</head>
<body>
<main class="canvas">

  <section class="card card--front" aria-label="Business card front">
    <div class="card__pattern" role="img" aria-label="Subtle tonal pattern of outlined geometric shapes across the blue card"></div>
    <div class="wordmark">
      <span class="wordmark__square"></span>
      <span>Quillbrook Networks Ltd.</span>
    </div>
  </section>

  <section class="card card--back" aria-label="Business card back">
    <div class="wordmark">
      <span class="wordmark__square"></span>
      <span>Quillbrook Networks Ltd.</span>
    </div>

    <div class="person">
      <p class="person__name">Daniel Harrow</p>
      <p class="person__title">Managing Director</p>
    </div>

    <ul class="contact">
      <li class="contact__item">
        <svg class="contact__icon" viewBox="0 0 20 16" aria-hidden="true">
          <path d="M2 4c0-2 4-3 8-3s8 1 8 3v1.5h-4V4H6v1.5H2z"/>
          <path d="M5 7h10l2 7H3z"/>
        </svg>
        <span>604-555-0148</span>
      </li>
      <li class="contact__item">
        <svg class="contact__icon" viewBox="0 0 20 16" aria-hidden="true">
          <circle cx="10" cy="8" r="7" fill="none" stroke="#1b87c9" stroke-width="1.6"/>
          <path d="M3 8h14M10 1c-3 4-3 10 0 14M10 1c3 4 3 10 0 14" fill="none" stroke="#1b87c9" stroke-width="1.4"/>
        </svg>
        <span>www.quillbrook.me</span>
      </li>
      <li class="contact__item">
        <svg class="contact__icon" viewBox="0 0 20 16" aria-hidden="true">
          <path d="M1 2h18v12H1z"/>
          <path d="M1 2l9 7 9-7" fill="none" stroke="#f4f4f4" stroke-width="1.6"/>
        </svg>
        <span>support@quillbrook.me</span>
      </li>
    </ul>

    <p class="tagline">
      <span class="tagline__rule"></span>
      <span>Revolutionizing IT Services</span>
      <span class="tagline__rule"></span>
    </p>
  </section>

</main>
</body>
</html>
```